Public Speaking Book for aspiring, ambitious speakers

I'm looking for a 6x9 book cover (Brivora standard) as well as ebook and audiobook formats.

I'm looking for orange font on a white background as these are my brand colours.

Feel free to use some yellow and gold too if you deem it appropriate.

Title: Climb and Kindle
Subtitle: Find Your Voice. Tell Your Story. Share your Message.
Author: Owen Thistlewood

I would like to have a picture of a female speaker on the front cover.

Alternatively, some kind of image that symbolises public speaking like a microphone, podium etc

Target Market(s)

Aspiring professional speakers

Colors
f78f20

Requirements
Must have
• Correct spelling!
Nice to have
• A logo or picture that fits the theme, but no pressure if you can't think of anything
Should not have
• No men in suits please. I don't want this to have a 1980s corporate look.

```html
<!DOCTYPE html>
<html lang="en">
<head>
<meta charset="utf-8">
<title>Climb and Kindle — Owen Thistlewood</title>
<link rel="stylesheet" href="https://fonts.googleapis.com/css2?family=Montserrat:wght@500;600&display=swap">
<style>
  :root {
    --cover-orange: #f78f20;
    --ink: #0a0a0a;
    --crowd-magenta: #c2185b;
    --crowd-purple: #5a1f6e;
    --crowd-teal: #1a9a8f;
    --crowd-red: #cf2a1c;
  }
  html, body {
    margin: 0;
    padding: 0;
    overflow: hidden;
    background: var(--cover-orange);
  }
  .cover {
    position: relative;
    width: 800px;
    height: 1200px;
    background: var(--cover-orange);
    font-family: "Montserrat", Arial, sans-serif;
    color: var(--ink);
    overflow: hidden;
  }
  .cover-title {
    position: absolute;
    top: 128px;
    left: 0;
    width: 100%;
    margin: 0;
    text-align: center;
    font-weight: 500;
    font-size: 122px;
    line-height: 110px;
    letter-spacing: 1px;
    text-transform: uppercase;
  }
  .cover-title span { display: block; }
  .crowd-illustration {
    position: absolute;
    left: 240px;
    top: 492px;
    width: 322px;
    height: 225px;
    border-radius: 110px;
    background: linear-gradient(135deg,
      var(--crowd-purple) 0%,
      var(--crowd-magenta) 35%,
      var(--crowd-red) 65%,
      var(--crowd-teal) 100%);
  }
  .cover-subtitle {
    position: absolute;
    top: 738px;
    left: 0;
    width: 100%;
    margin: 0;
    text-align: center;
    font-weight: 600;
    font-size: 31px;
    line-height: 43px;
    letter-spacing: 3px;
  }
  .cover-subtitle span { display: block; }
  .cover-author {
    position: absolute;
    top: 1062px;
    left: 0;
    width: 100%;
    margin: 0;
    text-align: center;
    font-weight: 600;
    font-size: 46px;
    letter-spacing: 1.5px;
  }
</style>
</head>
<body>
  <main class="cover">
    <h1 class="cover-title"><span>Climb and</span><span>Kindle</span></h1>

    <div class="crowd-illustration" role="img" aria-label="Illustration: a speech bubble filled with colourful silhouettes of a diverse crowd"></div>

    <p class="cover-subtitle">
      <span>Find Your Voice.</span>
      <span>Tell Your Story.</span>
      <span>Share your Message.</span>
    </p>

    <p class="cover-author">Owen Thistlewood</p>
  </main>
</body>
</html>
```